Fresh and unique Mortgage Broking business needs website design.

We need a professional yet fresh, bright and colourful website for my Mortgage broking business.
We specialise in the Non conforming/sub prime market with clients who have been rejected by other banks or have trouble getting finance through a traditional lender.
We are called Lark Lending and we aim to provide Hope to our clients when they have thought there was no hope.
I would like it to be on a Wordpress platform as I plan to do a lot of postings, both written and video and I need it to be easy to use.
I would also like it to be able to have a clear and simple enquiry box on the first page to capture contact details and notify me via email.

I have already had the logo designed in both green and black and a white version.
I have also had a a header made up using the white logo with leaves background that could possibly be used as the website header which I have used as my facebook header.

https://www.pagebook-example.com/MarcusDellowLark/

I tried playing around with a sitebuild website builder which kind of got some of the brightness and colours I was after but it had a lot to go.

http://larklending.sitebuildexample.com/

Industry/Entity Type

Finance

Number of Pages Required

4 page

Colors
0292cd
00a990
fbed22
ffc214
f78f20
ec1f27

Requirements
Nice to have
• I'm not sure what the difference between uncoded and coded website is so I'm not sure what I need?

```html
<!DOCTYPE html>
<html lang="en">
<head>
<meta charset="utf-8">
<title>Lark Lending</title>
<link href="https://fonts.googleapis.com/css2?family=Open+Sans:ital,wght@0,300;0,400;0,600;0,700;1,400&display=swap" rel="stylesheet">
<style>
:root{
  --red:#ec1f27;
  --orange:#f78f20;
  --teal:#00a990;
  --blue:#0292cd;
  --green:#1f7a3a;
  --ink:#333333;
  --body:#6a6a6a;
  --light:#ececec;
  --white:#ffffff;
}
*{box-sizing:border-box;margin:0;padding:0}
html,body{width:1200px;height:3557px;overflow:hidden}
body{font-family:"Open Sans",Arial,sans-serif;color:var(--body);background:var(--white);position:relative}
.abs{position:absolute}
.center{left:0;width:1200px;text-align:center}

/* hero */
.hero{position:absolute;left:0;top:0;width:1200px;height:640px;
  background:radial-gradient(ellipse at 30% 40%,#f3d8b8 0%,rgba(243,216,184,0) 45%),
  radial-gradient(ellipse at 75% 35%,#e9c9a4 0%,rgba(233,201,164,0) 40%),
  linear-gradient(180deg,#8a9a56 0%,#b8925f 40%,#9c6a4c 75%,#6e4d3d 100%)}
.hero-logo{left:60px;top:40px;color:var(--white);font-size:30px;font-weight:600;letter-spacing:.5px;display:flex;align-items:center;gap:12px}
.hero-logo .mark{width:20px;height:20px;border-radius:50%;background:var(--white)}
.nav{top:52px;left:0;width:1200px;font-size:12px;font-weight:600;color:var(--white);text-transform:uppercase}
.nav span{position:absolute}
.play{left:557px;top:249px;width:86px;height:86px}
.hero-title{top:348px;color:var(--white);font-weight:300;font-size:46px;line-height:1.2}
.hero-sub{top:405px;color:var(--white);font-weight:300;font-size:40px}

/* intro */
.intro-logo{top:722px;left:0;width:1200px;display:flex;justify-content:center;align-items:center;gap:18px;color:#333;font-size:40px;font-weight:400}
.intro-logo .mark{width:40px;height:40px;border-radius:50%;background:var(--green)}
.intro-text{top:850px;left:225px;width:750px;text-align:center;font-size:14.5px;line-height:26px}

/* services */
.section-title{font-size:40px;font-weight:300;color:#333}
.services-title{top:962px}
.services-sub{top:1035px;font-size:14.5px}
.service{top:1119px;width:250px}
.service .icon{width:86px;height:86px;border-radius:50%;display:flex;align-items:center;justify-content:center;margin-left:10px}
.service h3{font-size:16px;font-weight:600;color:#333;margin-top:34px}
.service p{font-size:12px;line-height:22px;margin-top:10px}
.dots{top:1391px;left:0;width:1200px;display:flex;justify-content:center;gap:6px}
.dots i{width:7px;height:7px;border-radius:50%;background:#ccc}
.dots i:first-child{background:#888}

/* property band */
.property{left:0;top:1468px;width:1200px;height:418px;
  background:radial-gradient(ellipse at 30% 55%,#c2571f 0%,rgba(194,87,31,0) 45%),
  radial-gradient(ellipse at 80% 30%,#8c2a12 0%,rgba(140,42,18,0) 45%),
  linear-gradient(90deg,#3a1a0d 0%,#7a3514 40%,#5a1f0c 70%,#1c0b05 100%)}
.property-title{top:1564px;color:var(--white);font-size:40px;font-weight:300}
.property-text{top:1632px;left:240px;width:720px;text-align:center;color:#f4e9e2;font-size:13.5px;line-height:24px}
.btn{background:var(--red);color:var(--white);font-size:12px;font-weight:700;text-transform:uppercase;display:flex;align-items:center;justify-content:center;width:142px;height:42px;border-radius:2px}

/* about */
.portrait-frame{left:100px;top:1973px;width:303px;height:299px;border:8px solid #e6e6e6;background:#fff;padding:6px}
.portrait{width:100%;height:100%;background:linear-gradient(180deg,#f5f5f5 0%,#d9c2ad 45%,#2d3644 80%,#1e2530 100%)}
.about-kicker{left:470px;top:1993px;font-size:22px;font-weight:600;color:#333}
.about-title{left:470px;top:2025px;font-size:32px;font-weight:300;color:#333}
.about-text{left:470px;top:2083px;width:610px;font-size:13.5px;line-height:24px}

/* blog */
.blog-title{top:2334px}
.post{top:2434px;width:322px}
.post .photo{width:322px;height:237px}
.post h3{font-size:15px;font-weight:700;color:#333;margin-top:22px}
.post .date{font-size:12px;font-style:italic;margin-top:8px;display:flex;align-items:center;gap:8px}
.post p{font-size:12.5px;line-height:24px;margin-top:6px}

/* testimonials */
.testimonials{left:0;top:2875px;width:1200px;height:379px;background:var(--light)}
.test-title{top:2912px;font-size:40px;font-weight:300;color:#444}
.quote-mark{top:2990px;font-size:54px;color:#c8c8c8;font-family:Georgia,serif;line-height:1}
.test-text{top:3055px;left:220px;width:760px;text-align:center;font-size:13.5px;font-style:italic;line-height:28px}
.arrow{top:3045px;color:#c8c8c8;font-size:28px}
.avatar{left:496px;top:3138px;width:66px;height:66px;border-radius:50%;border:3px solid #fff;background:linear-gradient(180deg,#e8e8e8,#c8b29e 50%,#364050)}
.client-name{left:581px;top:3147px;font-size:14px;font-weight:700;color:var(--red);text-transform:uppercase}
.client-role{left:581px;top:3174px;font-size:13px}

/* footer */
.foot-logo{left:100px;top:3380px;color:var(--green);font-size:26px;font-weight:600;display:flex;align-items:center;gap:8px}
.foot-logo .mark{width:18px;height:18px;border-radius:50%;background:var(--green)}
.foot-col{top:3314px;font-size:12px;color:#555}
.foot-col h4{font-size:13px;font-weight:700;color:#333;text-transform:uppercase;margin-bottom:14px;letter-spacing:.3px}
.foot-col li{list-style:none;line-height:23px}
.contact-line{display:flex;align-items:center;gap:10px}
.socials{display:flex;gap:8px;margin-top:14px}
.socials i{width:26px;height:26px;border-radius:50%}
.copyright{left:0;top:3510px;width:1200px;height:47px;background:#eeeeee;font-size:11.5px;display:flex;align-items:center;justify-content:center}
</style>
</head>
<body>

<div class="hero" role="img" aria-label="Photo of a smiling multi-generation family outdoors in warm sunlight"></div>
<div class="abs hero-logo"><span class="mark"></span>Lark Lending</div>
<div class="abs nav">
  <span style="left:476px">Home</span>
  <span style="left:576px">About Us</span>
  <span style="left:700px">Services</span>
  <span style="left:819px">Blog</span>
  <span style="left:900px">Testimonials</span>
  <span style="left:1061px">Contact Us</span>
</div>
<svg class="abs play" viewBox="0 0 86 86"><circle cx="43" cy="43" r="40" fill="rgba(255,255,255,.15)" stroke="#fff" stroke-width="4"/><path d="M34 26 L62 43 L34 60 Z" fill="#fff"/></svg>
<div class="abs center hero-title">Help for your finance</div>
<div class="abs center hero-sub">when all hope seems lost</div>

<div class="abs intro-logo"><span class="mark"></span>Lark Lending</div>
<p class="abs intro-text">We specialise in the Non conforming/sub prime market with clients who have been rejected by other banks or have trouble getting finance through a traditional lender.</p>

<h2 class="abs center section-title services-title">Our Services</h2>
<p class="abs center services-sub">We are called Lark Lending and we aim to give a fresh start to clients when they have thought there was no way.</p>

<div class="abs service" style="left:98px">
  <div class="icon" style="background:var(--red)"><svg width="44" height="44" viewBox="0 0 44 44" fill="none" stroke="#fff" stroke-width="2.4"><path d="M6 20 L22 7 L38 20"/><path d="M11 17 V37 H33 V17"/><text x="22" y="32" fill="#fff" stroke="none" font-size="14" font-family="Open Sans,sans-serif" font-weight="700" text-anchor="middle">$</text></svg></div>
  <h3>Residential loans</h3>
  <p>Lorem Ipsum is simply dummy text of the printing and typesetting industry. Lorem Ipsum has been the industry's standard</p>
</div>
<div class="abs service" style="left:366px">
  <div class="icon" style="background:var(--orange)"><svg width="44" height="44" viewBox="0 0 44 44" fill="none" stroke="#fff" stroke-width="2.4"><circle cx="22" cy="22" r="14"/><path d="M22 13 V31 M17 18 H25 a3 3 0 0 1 0 6 H19 a3 3 0 0 0 0 6 H27"/></svg></div>
  <h3>Investment loans</h3>
  <p>Lorem Ipsum is simply dummy text of the printing and typesetting industry. Lorem Ipsum has been the industry's standard</p>
</div>
<div class="abs service" style="left:634px">
  <div class="icon" style="background:var(--teal)"><svg width="44" height="44" viewBox="0 0 44 44" fill="none" stroke="#fff" stroke-width="2.4"><circle cx="22" cy="15" r="7"/><path d="M9 37 C9 28 15 24 22 24 C29 24 35 28 35 37"/></svg></div>
  <h3>Self employed loans</h3>
  <p>Lorem Ipsum is simply dummy text of the printing and typesetting industry. Lorem Ipsum has been the industry's standard</p>
</div>
<div class="abs service" style="left:902px">
  <div class="icon" style="background:var(--blue)"><svg width="44" height="44" viewBox="0 0 44 44" fill="none" stroke="#fff" stroke-width="2.4"><rect x="6" y="11" width="32" height="22" rx="2"/><path d="M11 19 H24 M11 25 H20 M28 22 H33"/></svg></div>
  <h3>Non confirming loans</h3>
  <p>Lorem Ipsum is simply dummy text of the printing and typesetting industry. Lorem Ipsum has been the industry's standard</p>
</div>
<div class="abs dots"><i></i><i></i><i></i><i></i></div>

<div class="abs property" role="img" aria-label="Close-up photo of orange autumn leaves against a dark background"></div>
<h2 class="abs center property-title">Property Advice</h2>
<p class="abs property-text">Marcus lives in Ashgrove and loves exploring the Ridgeview Shire with his wife and kids for great places to eat. With over 10 years' experience in financial services ranging from insurance, superannuation, investments and finance, Marcus bringing together his experience to provide a more holistic approach to his customers.</p>
<div class="abs btn" style="left:529px;top:1741px">Read More Info</div>

<div class="abs portrait-frame"><div class="portrait" role="img" aria-label="Portrait photo of the broker in a dark suit"></div></div>
<div class="abs about-kicker">Lark Lending is a Christian Mortgage Broking business.</div>
<div class="abs about-title">About Harbour Community Trust</div>
<p class="abs about-text">Marcus lives in Ashgrove and loves exploring the Ridgeview Shire with his wife and kids for great places to eat. With over 10 years' experience in financial services ranging from insurance, superannuation, investments and finance, Marcus bringing together his experience to provide a more holistic approach to his customers.</p>
<div class="abs btn" style="left:470px;top:2203px">Read More Info</div>

<h2 class="abs center section-title blog-title">Blog Posts</h2>
<div class="abs post" style="left:100px">
  <div class="photo" role="img" aria-label="Photo of a couple looking at a laptop at home" style="background:linear-gradient(135deg,#d9cfc4,#a38a75 55%,#6c5a4e)"></div>
  <h3>Lorem Ipsum is simply dummy text</h3>
  <div class="date"><svg width="12" height="12" viewBox="0 0 12 12" fill="none" stroke="#888" stroke-width="1.4"><rect x="1" y="2" width="10" height="9"/><path d="M1 5 H11 M4 0.5 V3 M8 0.5 V3"/></svg>03-May-2016</div>
  <p>Lorem Ipsum is simply dummy text of the printing and typesetting industry.</p>
</div>
<div class="abs post" style="left:439px">
  <div class="photo" role="img" aria-label="Photo of hands using a calculator over paperwork" style="background:linear-gradient(135deg,#f2f2f2,#c9c9c9 55%,#8e8e8e)"></div>
  <h3>Lorem Ipsum is simply dummy text</h3>
  <div class="date"><svg width="12" height="12" viewBox="0 0 12 12" fill="none" stroke="#888" stroke-width="1.4"><rect x="1" y="2" width="10" height="9"/><path d="M1 5 H11 M4 0.5 V3 M8 0.5 V3"/></svg>03-May-2016</div>
  <p>Lorem Ipsum is simply dummy text of the printing and typesetting industry.</p>
</div>
<div class="abs post" style="left:780px">
  <div class="photo" role="img" aria-label="Photo of a couple signing documents at a desk" style="background:linear-gradient(135deg,#eae6e0,#b8a595 50%,#3d4a62)"></div>
  <h3>Lorem Ipsum is simply dummy text</h3>
  <div class="date"><svg width="12" height="12" viewBox="0 0 12 12" fill="none" stroke="#888" stroke-width="1.4"><rect x="1" y="2" width="10" height="9"/><path d="M1 5 H11 M4 0.5 V3 M8 0.5 V3"/></svg>03-May-2016</div>
  <p>Lorem Ipsum is simply dummy text of the printing and typesetting industry.</p>
</div>

<div class="abs testimonials"></div>
<h2 class="abs center test-title">What our client's say</h2>
<div class="abs center quote-mark">&ldquo;</div>
<div class="abs arrow" style="left:148px">&#8249;</div>
<div class="abs arrow" style="left:1038px">&#8250;</div>
<p class="abs test-text">Lorem Ipsum is simply dummy text of the printing and typesetting industry. Lorem Ipsum has been the industry's standard dummy text ever since the 1500s, when an unknown printer took a galley of type and scrambled...</p>
<div class="abs avatar" role="img" aria-label="Client portrait photo"></div>
<div class="abs client-name">Dylan Marsh</div>
<div class="abs client-role">Business man</div>

<div class="abs foot-logo"><span class="mark"></span>Lark Lending</div>
<div class="abs foot-col" style="left:339px">
  <h4>Lark Lending</h4>
  <ul>
    <li>45 Example Lane | Springfield,</li>
    <li>CA 90000</li>
    <li class="contact-line"><svg width="12" height="12" viewBox="0 0 12 12" fill="var(--orange)"><path d="M2 1 L4.5 1 L5.5 4 L4 5 C5 7 6 8 8 8.5 L9 7 L11 8 L11 10.5 C6 11 1.5 6.5 2 1Z"/></svg>0400 000 123</li>
    <li class="contact-line"><svg width="12" height="12" viewBox="0 0 12 12" fill="var(--orange)"><rect x="1" y="4" width="10" height="6" rx="1"/><rect x="3" y="1" width="6" height="3"/></svg>(03) 9000 0456</li>
    <li class="contact-line"><svg width="12" height="12" viewBox="0 0 12 12" fill="none" stroke="var(--orange)" stroke-width="1.3"><rect x="1" y="2.5" width="10" height="7"/><path d="M1 2.5 L6 6.5 L11 2.5"/></svg>marcus@larklending.example</li>
  </ul>
</div>
<div class="abs foot-col" style="left:598px">
  <h4>Welcome</h4>
  <ul><li>Home</li><li>About Us</li><li>Services</li><li>Blog</li><li>Testimonials</li></ul>
</div>
<div class="abs foot-col" style="left:754px">
  <h4>Information</h4>
  <ul><li>Terms &amp; Conditions</li><li>Privacy policy</li><li>Disclaimer</li><li>Contact us</li><li>Sitemap</li></ul>
</div>
<div class="abs foot-col" style="left:932px">
  <h4>Social Media</h4>
  <ul><li>Connect with our social network</li></ul>
  <div class="socials">
    <i style="background:var(--blue)"></i><i style="background:var(--teal)"></i><i style="background:var(--orange)"></i><i style="background:#3fb3e6"></i><i style="background:var(--red)"></i>
  </div>
</div>
<div class="abs copyright">Copyright &copy; Lark Lending, 2016.All rights reserved.</div>

</body>
</html>
```